Slow Winter Song. A CD of beautiful 17th century music for lute played by a world famous lutenist.

Hi designers,
My name is Ollie Pellicott and I am an international lute player in need of a CD cover design. I am blind, so will be relying on other people's eyes and descriptions during the process, including yours! Are you up for the challenge?
My CD is called Slow Winter Song. It's beautiful lute music from the 17th century, very intimate and carming, but also very powerful.
I would like you to use the attached image, and find a way to include the following text in a tasteful way:
The text for the front cover is as follows:
Slow Winter Song
Oliver Pellicott - lute and theorbo
Music by Harcrane, Fennimore, Brackley, Tarn, Cavallenti and Ruhlendorf.
Here is a viewora link to some of the music I play, which should give you an idea:
www.viewora.net/olliepellicott1
Here is a link to my website, where you can see the covers of my other CDs, and get more information about me:
www.oliverpellicott.net
I'm excited to receive your design and ideas.
Best wishes
Ollie

```html
<!DOCTYPE html>
<html lang="en">
<head>
<meta charset="utf-8">
<title>Slow Winter Song — Oliver Pellicott</title>
<link rel="stylesheet" href="https://fonts.googleapis.com/css2?family=Herr+Von+Muellerhoff&family=Michroma&family=Arimo:wght@700&display=swap">
<style>
  :root {
    --paper: #e6e0d3;
    --paper-light: #efebe2;
    --band: #f1eee8;
    --ink: #111111;
    --ink-soft: #2a2a2a;
    --art-top: #f3f1ec;
    --art-bottom: #d9d4c8;
  }
  html, body {
    margin: 0;
    padding: 0;
    width: 1200px;
    height: 1200px;
    overflow: hidden;
    background: var(--paper);
  }
  .cover {
    position: relative;
    width: 1200px;
    height: 1200px;
    background: var(--paper);
    overflow: hidden;
  }
  .edge-band {
    position: absolute;
    left: 1087px;
    top: 0;
    width: 63px;
    height: 1200px;
    background: var(--band);
    opacity: 0.8;
  }
  .lute-art {
    position: absolute;
    left: 24px;
    top: 32px;
    width: 452px;
    height: 1111px;
  }
  .title-block {
    position: absolute;
    left: 300px;
    top: 20px;
    width: 780px;
    text-align: center;
  }
  .album-title {
    margin: 0;
    font-family: "Herr Von Muellerhoff", cursive;
    font-weight: 400;
    font-size: 215px;
    line-height: 200px;
    color: var(--ink);
  }
  .album-title span { display: block; }
  .album-subtitle {
    margin: 22px 0 0;
    font-family: "Herr Von Muellerhoff", cursive;
    font-size: 48px;
    color: var(--ink-soft);
  }
  .artist {
    position: absolute;
    left: 470px;
    top: 828px;
    width: 600px;
    text-align: center;
    font-family: "Michroma", sans-serif;
    font-size: 24px;
    line-height: 40px;
    letter-spacing: 1px;
    color: var(--ink);
    text-transform: uppercase;
  }
  .composers {
    position: absolute;
    left: 470px;
    top: 975px;
    width: 600px;
    text-align: center;
    font-family: "Arimo", sans-serif;
    font-weight: 700;
    font-size: 21px;
    line-height: 30px;
    color: var(--ink);
    text-transform: uppercase;
  }
  .composers p { margin: 0; }
</style>
</head>
<body>
  <main class="cover">
    <div class="edge-band"></div>

    <svg class="lute-art" viewBox="0 0 452 1111" role="img" aria-label="Engraved drawing of a lute with a bent-back pegbox, shown upright">
      <defs>
        <linearGradient id="luteTone" x1="0" y1="0" x2="0" y2="1">
          <stop offset="0" stop-color="var(--art-top)"/>
          <stop offset="1" stop-color="var(--art-bottom)"/>
        </linearGradient>
      </defs>
      <rect x="0" y="0" width="452" height="1111" rx="6" fill="url(#luteTone)"/>
    </svg>

    <header class="title-block">
      <h1 class="album-title">
        <span>Slow</span>
        <span>Winter</span>
        <span>Song</span>
      </h1>
      <p class="album-subtitle">17th century music for lute</p>
    </header>

    <div class="artist">
      <div>Oliver Pellicott</div>
      <div>Lute and Theorbo</div>
    </div>

    <div class="composers">
      <p>Music by:</p>
      <p>Harcrane • Fennimore • Brackley</p>
      <p>Tarn • Cavallenti • Ruhlendorf</p>
    </div>
  </main>
</body>
</html>
```